Business Card Design

We need the business card for our new business based in St. Marys, we manufacture mainly bubble wraps. And we would like the design to use our company logo and also make it easy for people to understand right away we are bubble wrap manufacturer

Industry/Entity Type

Business

Contact Information for Business Card

Cushtane Pty Ltd, 14 Larkin Road St. Marys NSW 2760, Tel: 02 9471 5826, Fax: 9471 5839, Dara Oyelaran, General Manager, Mobile :0438 217 564, dara.oyelaran@cushtane.com.au, Website: cushtane.com.au

```html
<!DOCTYPE html>
<html lang="en">
<head>
<meta charset="utf-8">
<title>Cushtane Pty Ltd – Business Card</title>
<link rel="stylesheet" href="https://fonts.googleapis.com/css2?family=Exo+2:wght@300;400;500;700&display=swap">
<style>
  :root {
    --red: #c8232f;
    --red-dark: #a81b26;
    --white: #ffffff;
    --paper: #f7f7f7;
    --grey: #7b7b7b;
    --grey-light: #8e8e8e;
    --backdrop: #e8e5e0;
  }
  * { box-sizing: border-box; margin: 0; padding: 0; }
  html, body {
    width: 1200px; height: 885px; overflow: hidden;
    background: var(--backdrop);
    font-family: "Exo 2", sans-serif;
  }
  .card {
    position: absolute; left: 300px;
    width: 600px; height: 367px;
    border-radius: 4px;
    box-shadow: 0 6px 18px rgba(0,0,0,0.18);
    overflow: hidden;
  }
  /* Front */
  .card--front { top: 40px; background: linear-gradient(180deg, var(--white), var(--paper)); }
  .front__brand { position: absolute; left: 38px; top: 150px; }
  .brand-name {
    font-weight: 700; font-size: 42px; letter-spacing: 0.02em;
    color: var(--grey); line-height: 1;
  }
  .brand-tagline {
    margin-top: 8px; font-size: 9.5px; font-weight: 400;
    letter-spacing: 0.32em; color: var(--grey-light); text-transform: uppercase;
  }
  .front__divider {
    position: absolute; left: 298px; top: 104px;
    width: 1px; height: 180px; background: var(--red);
  }
  .front__person { position: absolute; left: 312px; top: 32px; }
  .person-name { font-size: 30px; font-weight: 400; color: var(--red); line-height: 1.1; }
  .person-title { font-size: 20px; font-weight: 300; color: var(--grey); line-height: 1.2; }
  .contact-list { position: absolute; left: 312px; top: 120px; list-style: none; }
  .contact-list li {
    display: flex; align-items: center; gap: 10px;
    height: 32px; font-size: 16px; font-weight: 300; color: var(--grey);
  }
  .contact-icon { width: 18px; height: 18px; flex: none; }
  .front__band {
    position: absolute; left: 0; bottom: 0; width: 100%; height: 62px;
    background: linear-gradient(90deg, var(--red-dark), var(--red));
    display: flex; align-items: center; justify-content: center;
    color: var(--white); font-size: 22px; font-weight: 500;
  }
  /* Back */
  .card--back {
    top: 478px;
    background: radial-gradient(ellipse at 40% 35%, #d42b37, var(--red-dark));
    display: flex; flex-direction: column; align-items: center; justify-content: center;
  }
  .back__name {
    font-weight: 700; font-size: 84px; letter-spacing: 0.02em;
    color: var(--white); line-height: 1;
  }
  .back__tagline {
    margin-top: 16px; font-size: 15px; font-weight: 400;
    letter-spacing: 0.38em; color: var(--white); text-transform: uppercase;
  }
</style>
</head>
<body>

<section class="card card--front" aria-label="Business card front">
  <div class="front__person">
    <p class="person-name">Dara Oyelaran</p>
    <p class="person-title">General Manager</p>
  </div>

  <div class="front__divider"></div>

  <ul class="contact-list">
    <li>
      <svg class="contact-icon" viewBox="0 0 18 18" aria-hidden="true"><rect width="18" height="18" rx="2" fill="var(--red)"/><path d="M5 4h3l1 3-1.5 1a7 7 0 0 0 2.5 2.5L11 9l3 1v3c-5 0-9-4-9-9z" fill="#fff"/></svg>
      02 9471 5826
    </li>
    <li>
      <svg class="contact-icon" viewBox="0 0 18 18" aria-hidden="true"><rect width="18" height="18" rx="2" fill="var(--red)"/><rect x="6" y="3.5" width="6" height="11" rx="1" fill="none" stroke="#fff" stroke-width="1.3"/><circle cx="9" cy="12.6" r="0.7" fill="#fff"/></svg>
      0438 217 564
    </li>
    <li>
      <svg class="contact-icon" viewBox="0 0 18 18" aria-hidden="true"><rect width="18" height="18" rx="2" fill="var(--red)"/><rect x="4" y="7" width="10" height="6.5" fill="none" stroke="#fff" stroke-width="1.3"/><rect x="6" y="4" width="6" height="3" fill="#fff"/><line x1="6" y1="10.5" x2="12" y2="10.5" stroke="#fff" stroke-width="1"/></svg>
      9471 5839
    </li>
    <li>
      <svg class="contact-icon" viewBox="0 0 18 18" aria-hidden="true"><rect width="18" height="18" rx="2" fill="var(--red)"/><circle cx="9" cy="9" r="5" fill="none" stroke="#fff" stroke-width="1.2"/><ellipse cx="9" cy="9" rx="2.2" ry="5" fill="none" stroke="#fff" stroke-width="1"/><line x1="4" y1="9" x2="14" y2="9" stroke="#fff" stroke-width="1"/></svg>
      cushtane.com.au
    </li>
    <li>
      <svg class="contact-icon" viewBox="0 0 18 18" aria-hidden="true"><rect width="18" height="18" rx="2" fill="var(--red)"/><rect x="3.5" y="5" width="11" height="8" fill="none" stroke="#fff" stroke-width="1.2"/><path d="M3.5 5l5.5 4.5 5.5-4.5" fill="none" stroke="#fff" stroke-width="1.2"/></svg>
      dara.oyelaran@cushtane.com.au
    </li>
  </ul>

  <div class="front__brand">
    <p class="brand-name">CUSHTANE</p>
    <p class="brand-tagline">Bubble Wrap Manufacturers</p>
  </div>

  <div class="front__band">14 Larkin Road Orwin Vale NSW 2784</div>
</section>

<section class="card card--back" aria-label="Business card back">
  <p class="back__name">CUSHTANE</p>
  <p class="back__tagline">Bubble Wrap Manufacturers</p>
</section>

</body>
</html>
```